Company raising consciousness thru leadership & self-awareness needs amazing Letterhead

We are a technology company that spun out of a consulting firm. We are waking people up in corporate America through surveys, leadership development, workshops and consulting. Getting employees to become self-aware and changing company culture through improved leadership and team effectiveness. We need Word letterhead for our proposals, handouts, and worksheets that match our brand standard, is fresh, and communicates trust, credibility and professionalism.

Our target clients are other businesses, and executive leaders and C-suite leaders in those companies.

Sans Serif

• A Word template we can use for handouts, proposals, executive summary, project management documents, and letters. We need our logo. Please add page number and date on the footer. Must match the theme of our new website in look and feel to match the brand we are trying to promote. Use the colors from our brand standard document I submitted.

```html
<!DOCTYPE html>
<html lang="en">
<head>
<meta charset="utf-8">
<title>Lumera Collective – Letterhead</title>
<link rel="stylesheet" href="https://fonts.googleapis.com/css2?family=Open+Sans:wght@400;600&family=Roboto:wght@400&display=swap">
<style>
  :root {
    --backdrop: #e9e9eb;
    --paper: #f7f7f7;
    --ink: #4a4a4f;
    --ink-dark: #2c2c33;
    --navy: #2b4a86;
    --purple: #7b4aa0;
    --sign-tone: #e2e2e4;
  }
  * { box-sizing: border-box; margin: 0; padding: 0; }
  html, body {
    width: 1200px; height: 795px; overflow: hidden;
    background: var(--backdrop);
  }
  .canvas {
    position: relative; width: 1200px; height: 795px;
    display: flex; align-items: center; justify-content: center;
  }
  .letterhead {
    position: relative;
    width: 534px; height: 755px;
    background: var(--paper);
    box-shadow: 0 2px 10px rgba(0,0,0,0.08);
    font-family: 'Open Sans', sans-serif;
    color: var(--ink);
  }
  .brand {
    position: absolute; left: 46px; top: 84px;
  }
  .brand-name {
    font-family: 'Open Sans', sans-serif;
    font-weight: 600; font-size: 15px; letter-spacing: 0.03em;
    color: var(--navy); line-height: 1.2;
  }
  .contact {
    position: absolute; right: 46px; top: 36px;
    padding-left: 12px;
    border-left: 1px solid var(--purple);
    font-family: 'Roboto', sans-serif; font-style: normal;
    font-size: 10.5px; line-height: 1.3; color: var(--ink-dark);
  }
  .contact-line { display: flex; align-items: center; gap: 5px; }
  .contact-line svg { width: 9px; height: 9px; flex: none; }
  .letter-body {
    position: absolute; left: 118px; top: 182px; width: 372px;
    font-size: 8.9px; line-height: 1.45;
  }
  .salutation { margin-bottom: 12px; }
  .paragraph { margin-bottom: 14px; }
  .closing { margin-top: 6px; }
  .signature-area {
    margin-top: 10px; width: 92px; height: 46px;
    background: var(--sign-tone); border-radius: 3px;
  }
  .footer-band {
    position: absolute; left: 0; bottom: 0; width: 100%; height: 7px;
  }
</style>
</head>
<body>
<main class="canvas">
  <article class="letterhead">
    <header>
      <div class="brand">
        <span class="brand-name">Lumera Collective</span>
      </div>
      <address class="contact">
        <div>48 Alder Brook Lane,</div>
        <div>Suite 310, Fairhaven,</div>
        <div>NY 10982</div>
        <div class="contact-line">
          <svg viewBox="0 0 10 10"><path d="M2 1l2 2-1 1.5c.7 1.3 1.2 1.8 2.5 2.5L7 6l2 2-1.5 1.5C4.5 9 1 5.5.5 2.5z" fill="var(--navy)"/></svg>
          555-210-4478
        </div>
        <div class="contact-line">
          <svg viewBox="0 0 10 10"><rect x="0.5" y="2" width="9" height="6" fill="var(--navy)"/><path d="M.5 2l4.5 3.5L9.5 2" stroke="#fff" stroke-width="0.8" fill="none"/></svg>
          hello@lumeramail.com
        </div>
        <div class="contact-line">
          <svg viewBox="0 0 10 10"><circle cx="5" cy="5" r="4.5" fill="var(--navy)"/><path d="M.5 5h9M5 .5c-2 2.5-2 6.5 0 9M5 .5c2 2.5 2 6.5 0 9" stroke="#fff" stroke-width="0.6" fill="none"/></svg>
          www.lumeraweb.com
        </div>
      </address>
    </header>

    <section class="letter-body">
      <p class="salutation">Dear customer,</p>
      <p class="paragraph">Lorem ipsum dolor sit amet, consectetur adipisicing elit, sed do eiusmod tempor incididunt ut labore et dolore magna aliqua. Ut enim ad minim veniam, quis nostrud exercitation ullamco laboris nisi ut aliquip ex ea commodo consequat. Duis aute irure dolor in reprehenderit in voluptate velit esse cillum dolore eu fugiat nulla pariatur. Excepteur sint occaecat cupidatat non proident, sunt in culpa qui officia deserunt mollit anim id est laborum.</p>
      <p class="paragraph">Lorem ipsum dolor sit amet, consectetur adipisicing elit, sed do eiusmod tempor incididunt ut labore et dolore magna aliqua. Ut enim ad minim veniam, quis nostrud exercitation ullamco laboris nisi ut aliquip ex ea commodo consequat. Duis aute irure dolor in reprehenderit in voluptate velit esse cillum dolore eu fugiat nulla pariatur. Excepteur sint occaecat cupidatat non proident, sunt in culpa qui officia deserunt mollit anim id est laborum.</p>
      <p class="paragraph">Lorem ipsum dolor sit amet, consectetur adipisicing elit, sed do eiusmod tempor incididunt ut labore et dolore magna aliqua. Ut enim ad minim veniam, quis nostrud exercitation ullamco laboris nisi ut aliquip ex ea commodo consequat. Duis aute irure dolor in reprehenderit in voluptate velit esse cillum dolore eu fugiat nulla pariatur. Excepteur sint occaecat cupidatat non proident, sunt in culpa qui officia deserunt mollit anim id est laborum.</p>
      <p class="paragraph">Lorem ipsum dolor sit amet, consectetur adipisicing elit, sed do eiusmod tempor incididunt ut labore et dolore magna aliqua. Ut enim ad minim veniam, quis nostrud exercitation ullamco laboris nisi ut aliquip ex ea commodo consequat. Duis aute irure dolor in reprehenderit.</p>
      <p class="closing">Yours Sincerely,</p>
      <div class="signature-area" role="img" aria-label="Handwritten signature of the sender"></div>
    </section>

    <svg class="footer-band" viewBox="0 0 534 7" preserveAspectRatio="none" aria-hidden="true">
      <polygon points="0,0 326,0 322,7 0,7" fill="var(--navy)"/>
      <polygon points="328,0 534,0 534,7 324,7" fill="var(--purple)"/>
    </svg>
  </article>
</main>
</body>
</html>
```